Rehabilitation Centre Driving Evaluation brochure

I have already designed a brochure when I was at my previous workplace, but need a new one for my own rehab clinic. I will attach the brochure that I already did, as the information hasn't really changed. It is just very old and very ugly. It is an information pamphlet that will be in physician offices. Please let me know if you need anything else.

Target Market(s)

physicians, rehabilitation professionals, therapists, and individuals with medical conditions who want to return to driving

Industry/Entity Type

Medical

Requirements
Nice to have
• I am not stuck on the trifold, and actually may prefer a single fold brochure.

```html
<!DOCTYPE html>
<html lang="en">
<head>
<meta charset="utf-8">
<title>Driving Evaluation and Training Center – Brochure</title>
<link href="https://fonts.googleapis.com/css2?family=Questrial&family=Oswald:wght@600&display=swap" rel="stylesheet">
<style>
  :root{
    --stage:#e9e9ea;
    --ink-dark:#0b141c;
    --navy:#17425f;
    --heading-blue:#1d4b6f;
    --lime:#b8c40a;
    --white:#ffffff;
    --body-light:#e6e8ea;
    --body-dark:#222a30;
    --body-grey:#5d646a;
    --muted:#8a9096;
  }
  *{box-sizing:border-box;margin:0;padding:0}
  html,body{width:989px;height:1200px;overflow:hidden}
  body{background:var(--stage);font-family:"Questrial",sans-serif;position:relative}

  .panel{position:absolute;left:114px;width:760px;height:537px;overflow:hidden}
  .panel--outside{top:41px;background:var(--ink-dark)}
  .panel--inside{top:622px;background:var(--white)}

  /* outside: back cover */
  .back-cover{position:absolute;left:0;top:0;width:378px;height:100%;
    background:linear-gradient(160deg,#112a3c 0%,#0b1722 35%,#060a0e 100%)}
  .section-title{font-weight:400;font-size:15px;letter-spacing:.2px}
  .back-cover .section-title{position:absolute;left:35px;top:57px;color:var(--lime)}
  .back-cover .copy{position:absolute;left:35px;width:310px;color:var(--body-light);font-size:9.4px;line-height:11.4px}
  .back-cover .copy--one{top:90px}
  .back-cover .copy--two{top:170px}

  .wordmark{display:flex;align-items:center;gap:8px;color:var(--lime);font-size:17px;line-height:19px}
  .wordmark__dot{width:12px;height:12px;border-radius:50%;background:var(--lime);flex:none}
  .back-cover .wordmark{position:absolute;left:36px;top:318px}

  .contact{position:absolute;left:70px;top:402px;list-style:none;color:var(--body-light);font-size:10.4px;line-height:12px}
  .contact li{display:flex;align-items:flex-start;gap:8px;margin-bottom:5px}
  .contact li.contact__address{margin-bottom:8px}
  .contact svg{width:11px;height:11px;flex:none;margin-top:1px}

  /* outside: front cover */
  .front-cover{position:absolute;left:378px;top:0;width:382px;height:100%;
    background:linear-gradient(180deg,#cfd1cf 0%,#8e938f 28%,#4c534f 52%,#2b2e2d 72%,#121414 100%)}
  .front-cover .wordmark{position:absolute;left:28px;top:42px;color:var(--lime)}
  .cover-title{position:absolute;left:22px;top:396px;font-family:"Oswald",sans-serif;font-weight:600;font-size:31px;line-height:34px;letter-spacing:-.6px;text-transform:uppercase}
  .cover-title span{display:block;color:var(--white)}
  .cover-title span.cover-title__accent{color:var(--lime)}
  .cover-subtitle{position:absolute;left:24px;top:472px;color:var(--white);font-size:14.6px;letter-spacing:.2px}
  .cover-url{position:absolute;left:25px;top:508px;color:var(--muted);font-size:10px}

  /* inside */
  .inside-backdrop{position:absolute;left:0;top:210px;width:100%;height:327px;
    background:linear-gradient(180deg,rgba(255,255,255,0) 0%,#eef0f1 45%,#d9dde0 100%)}
  .top-band{position:absolute;left:0;top:0;width:100%;height:50px;background:var(--navy)}
  .top-band .section-title{position:absolute;left:79px;top:27px;color:var(--white)}
  .bottom-band{position:absolute;left:0;bottom:0;width:100%;height:8px;background:var(--navy)}

  .emblem{position:absolute;left:14px;top:58px;width:66px;height:84px;
    background:linear-gradient(180deg,#d0d0d0,#9a9a9a);border-radius:6px}
  .reason-copy{position:absolute;left:87px;width:276px;color:var(--body-dark);font-size:9px;line-height:10.8px}
  .reason-copy--one{top:60px}
  .reason-copy--two{top:136px}

  .eligibility{position:absolute;left:18px;top:224px;width:348px;height:86px;background:var(--lime);border-radius:8px;padding:12px 13px}
  .eligibility .section-title{color:var(--white);margin-bottom:6px}
  .eligibility p{color:var(--white);font-size:9px;line-height:10.8px}

  .what-we-do{position:absolute;left:21px;top:340px;width:345px}
  .what-we-do .section-title{color:var(--heading-blue);margin-bottom:9px}
  .what-we-do p{color:var(--body-dark);font-size:9px;line-height:10.8px;margin-bottom:9px}

  .driver-photo{position:absolute;left:402px;top:28px;width:336px;height:83px;border-radius:8px;
    background:linear-gradient(100deg,#f2d9a6 0%,#c89a62 25%,#6e5a48 45%,#2c2e32 70%,#1b1d21 100%)}

  .services{position:absolute;left:404px;top:126px;width:330px}
  .services .section-title{color:var(--heading-blue);margin-bottom:11px}
  .service{margin-bottom:0}
  .service h3{color:var(--heading-blue);font-weight:400;font-size:11.4px;-webkit-text-stroke:.35px var(--heading-blue);margin-bottom:5px}
  .service p{color:var(--body-grey);font-size:8.9px;line-height:10.8px}
  .service--clinical{margin-bottom:28px}
  .service--road{margin-bottom:23px}
  .service--equipment{margin-bottom:23px}
</style>
</head>
<body>

<section class="panel panel--outside">
  <div class="back-cover">
    <h2 class="section-title">Referral Process</h2>
    <p class="copy copy--one">Referrals may be made by physicians, therapists, individuals requiring service, insurance companies, case managers, community service agencies, etc. The referral source will be asked to complete a referral form. The client’s physician will be contacted and asked to complete a medical referral form stating the client is medically able to participate in the assessment.</p>
    <p class="copy copy--two">Referrals can be made for any individual who requires an evaluation of their driving skills or adaptive equipment needs by contacting us.</p>

    <div class="wordmark"><span class="wordmark__dot"></span><span>Northvale<br>Rehabilitation Associates</span></div>

    <ul class="contact">
      <li class="contact__address">
        <svg viewBox="0 0 12 12"><path d="M6 11.5S2 7 2 4.5a4 4 0 0 1 8 0C10 7 6 11.5 6 11.5z" fill="none" stroke="#b8c40a" stroke-width="1.2"/><circle cx="6" cy="4.5" r="1.4" fill="#b8c40a"/></svg>
        <span>420 Maplecrest Road, Unit #5<br>Riverton, Ontario, N0R 2B4</span>
      </li>
      <li>
        <svg viewBox="0 0 12 12"><path d="M2.5 1h2l1 2.6-1.3.9a6 6 0 0 0 3.3 3.3l.9-1.3 2.6 1v2c0 .8-.6 1.4-1.4 1.4A9.5 9.5 0 0 1 1 2.4C1 1.6 1.7 1 2.5 1z" fill="#b8c40a"/></svg>
        <span>555 014 2290</span>
      </li>
      <li>
        <svg viewBox="0 0 12 12"><rect x="3" y="1" width="6" height="3" fill="#b8c40a"/><rect x="1" y="4.5" width="10" height="4.5" rx="1" fill="#b8c40a"/><rect x="3" y="7.5" width="6" height="3.5" fill="#fff" stroke="#b8c40a"/></svg>
        <span>555 014 2291</span>
      </li>
      <li>
        <svg viewBox="0 0 12 12"><rect x="1" y="2.5" width="10" height="7" fill="none" stroke="#b8c40a" stroke-width="1.1"/><path d="M1 2.5l5 4 5-4" fill="none" stroke="#b8c40a" stroke-width="1.1"/></svg>
        <span>office@northvalerehab.ca</span>
      </li>
      <li>
        <svg viewBox="0 0 12 12"><circle cx="6" cy="6" r="5" fill="none" stroke="#b8c40a" stroke-width="1.1"/><ellipse cx="6" cy="6" rx="2.2" ry="5" fill="none" stroke="#b8c40a" stroke-width="1"/><path d="M1 6h10" stroke="#b8c40a" stroke-width="1"/></svg>
        <span>www.northvalerehab.ca</span>
      </li>
    </ul>
  </div>

  <div class="front-cover" role="img" aria-label="Photograph of a car driving along a misty forest road">
    <div class="wordmark"><span class="wordmark__dot"></span><span>Northvale<br>Rehabilitation Associates</span></div>
    <h1 class="cover-title"><span>Driving Evaluation</span><span class="cover-title__accent">and Training Center</span></h1>
    <p class="cover-subtitle">A comprehensive driver rehabilitation program</p>
    <p class="cover-url">www.northvalerehab.ca</p>
  </div>
</section>

<section class="panel panel--inside">
  <div class="inside-backdrop" role="img" aria-label="Faded photograph of an open highway"></div>
  <div class="top-band"><h2 class="section-title">Reason for Assessment</h2></div>

  <div class="emblem" role="img" aria-label="Medical caduceus emblem"></div>
  <p class="reason-copy reason-copy--one">Each physician is required by law to report to the Ministry of Transportation any individual whose driving skills may be affected as a result of illness or injury. Therefore, the client’s driver’s licence may be placed under medical suspension. If this occurs, the client will be asked to undergo a driving evaluation from an Ontario Driver Assessment Centre.</p>
  <p class="reason-copy reason-copy--two">Individuals affected by illness, injury, or the aging process, whose driving skills have the potential to be affected, are also encouraged to undergo an evaluation of driving skills. The evaluation is designed to assess each client’s ability to safely operate a motor vehicle and provide recommendations as needed.</p>

  <div class="eligibility">
    <h2 class="section-title">Eligibility</h2>
    <p>Most individuals with disabilities are eligible for an evaluation of their ability to drive. Clients must have a valid driver’s licence or the ability to obtain a temporary driver’s licence or learner’s permit.</p>
  </div>

  <div class="what-we-do">
    <h2 class="section-title">What we do?</h2>
    <p>Northvale Rehabilitation Associates is committed to providing optimal rehabilitation service in a cost effective manner.</p>
    <p>We offer a multi-disciplinary, client-centred program of assessment, treatment and consultation for clients with physical, cognitive and/or perceptual impairments. We are aware each client is unique, therefore each program is tailored according to the individual’s needs and personal goals.</p>
    <p>The driving assessment and training program is part of our comprehensive rehabilitation services. It is a service which represents our dedication to assist all individuals achieve optimal independence. Driving is an integral skill which is often essential for independence in the community.</p>
  </div>

  <div class="driver-photo" role="img" aria-label="Photograph of a hand on a steering wheel at sunset"></div>

  <div class="services">
    <h2 class="section-title">Program Components &amp; Services</h2>
    <div class="service service--clinical">
      <h3>Clinical Evaluation</h3>
      <p>The client is assessed by a certified occupational therapist. The client is initially seen in clinic for an assessment of physical, cognitive, and perceptual functioning as they relate to driving. The in-clinic portion of the assessment provides the therapist with information regarding medical history, driving history, knowledge of road signs and driving rules, physical abilities, cognitive status, visual and perceptual skills.</p>
    </div>
    <div class="service service--road">
      <h3>On the Road Evaluation</h3>
      <p>Following the in-clinic assessment, each client is then assessed in car by the therapist together with a certified driving instructor. This portion of the evaluation provides valuable information regarding the individual’s functional driving skills.</p>
    </div>
    <div class="service service--equipment">
      <h3>Evaluation Equipment Needs</h3>
      <p>During the evaluation, it will be determined whether adaptive equipment will be necessary to improve the client’s ability to drive safely. Recommendations will be made for adaptive equipment and installation.</p>
    </div>
    <div class="service">
      <h3>Training &amp; Follow-up Services</h3>
      <p>Clients are commonly seen following a driving evaluation for training with driving skills or adaptive equipment. Further involvement with the occupational therapist may be indicated for cognitive or perceptual retraining, mobility-aid prescription, vehicle modification, or consultation with appropriate new vehicle purchase.</p>
    </div>
  </div>

  <div class="bottom-band"></div>
</section>

</body>
</html>
```